Website mockup using figma or other design software for Plumbing Company

We are looking for a talented UI/UX designer to create a high-converting, modern, and professional website design for a local plumbing company. The goal is to move away from the "dated" look of traditional trades and provide a seamless, trustworthy experience for homeowners and commercial clients.
The Challenge
Create a Homepage and a Service Page design that balances professional expertise with an urgent "call-to-action" (CTA) focus. We need a design that looks great on desktop but is built with a mobile-first mindset, as most customers find plumbers via their phones during emergencies.
This company will focus more on B2B, and corporate contracts, but should still be friendly to the public.
Here are some examples of what we are looking for
https://velotrin-works.com/construction/plumbing-construction/
https://velotrin-works.com/
The company is called "KT Plumbing."
Please see the logo below.

```html
<!DOCTYPE html>
<html lang="en">
<head>
<meta charset="utf-8">
<title>KT Plumbing</title>
<link href="https://fonts.googleapis.com/css2?family=Montserrat:wght@600;700;800&family=Roboto:ital,wght@0,400;0,500;0,700;1,400&display=swap" rel="stylesheet">
<style>
:root{
  --orange:#c8663f;
  --sage:#b2c3b9;
  --sage-dark:#9fb0a6;
  --ink:#1f2326;
  --text:#5c6266;
  --muted:#8a8f93;
  --footer:#27343a;
  --footer-panel:#2f3d44;
  --white:#ffffff;
  --line:#e4e6e7;
}
*{box-sizing:border-box;margin:0;padding:0}
html,body{width:1200px;height:5059px;overflow:hidden}
body{position:relative;background:var(--white);font-family:'Roboto',sans-serif;color:var(--text)}
.abs{position:absolute}
h2.section-title{position:absolute;left:0;width:1200px;text-align:center;font-family:'Montserrat',sans-serif;font-weight:800;font-size:37px;color:var(--ink);letter-spacing:.3px}
.btn{position:absolute;display:flex;align-items:center;justify-content:center;background:var(--orange);color:#fff;font-family:'Roboto',sans-serif;font-weight:700;font-size:14px;letter-spacing:.3px;clip-path:polygon(6% 0,100% 0,94% 100%,0 100%)}

/* top bar */
.topbar-left{left:0;top:0;width:655px;height:34px;background:var(--sage-dark)}
.social-dot{position:absolute;top:6px;width:22px;height:22px;border-radius:50%;border:1.5px solid #fff}
.topbar-right{left:655px;top:0;width:545px;height:34px;background:var(--footer);color:#fff;font-size:14px;display:flex;align-items:center;padding-left:38px;gap:8px}
.topbar-right svg{flex:none}

/* nav */
.nav{left:0;top:34px;width:1200px;height:98px;background:#fff;box-shadow:0 2px 6px rgba(0,0,0,.05)}
.brand{position:absolute;left:145px;top:30px;display:flex;align-items:center;gap:10px;font-family:'Montserrat',sans-serif;font-weight:800;font-size:22px;color:var(--ink)}
.brand-mark{width:26px;height:26px;background:var(--ink)}
.menu{position:absolute;top:44px;font-family:'Roboto',sans-serif;font-weight:500;font-size:14px;color:var(--ink)}
.menu.active:after{content:"";position:absolute;left:0;right:0;bottom:-6px;height:2px;background:var(--orange)}

/* hero */
.hero-photo{left:0;top:132px;width:1200px;height:685px;background:linear-gradient(100deg,#4a3a33 0%,#8d4b3f 18%,#6f7f86 38%,#c9c9c4 58%,#e4e2dc 78%,#cfcdc6 100%)}
.hero-card{left:595px;top:304px;width:511px;height:334px;background:rgba(255,255,255,.88)}
.hero-title{left:652px;top:345px;font-family:'Montserrat',sans-serif;font-weight:800;font-size:36px;line-height:42px;color:var(--ink)}
.hero-sub{left:652px;top:451px;width:420px;font-size:18px;line-height:30px;color:#454a4e}

/* about */
.about-title{left:143px;top:912px;font-family:'Montserrat',sans-serif;font-weight:800;font-size:37px;color:var(--ink)}
.about-text{left:145px;top:982px;width:464px;font-size:14.5px;line-height:28px;color:var(--text);text-align:justify}
.about-photo{left:666px;top:911px;width:493px;height:385px;border-radius:14px;background:linear-gradient(135deg,#dfe3e4 0%,#b9c6cf 40%,#5f7f9e 60%,#e8eaea 80%,#9a9fa1 100%)}

/* services */
.services-band{left:0;top:1402px;width:1200px;height:747px;background:var(--sage)}
.services-sub{left:0;top:1589px;width:1200px;text-align:center;font-size:16px;color:#4f5a56}
.service-card{position:absolute;width:293px;background:#fff;border-radius:6px;display:flex;flex-direction:column;align-items:center;justify-content:center;gap:14px;font-family:'Roboto',sans-serif;font-weight:500;font-size:16px;color:var(--ink);text-align:center;line-height:22px}
.service-card.raised{box-shadow:0 0 0 4px rgba(255,255,255,.5),0 8px 18px rgba(0,0,0,.12)}

/* why */
.why-item{position:absolute;width:300px;text-align:center}
.why-item svg{display:block;margin:0 auto}
.why-item h3{margin-top:12px;font-family:'Roboto',sans-serif;font-weight:500;font-size:17px;color:var(--ink)}
.why-item p{margin-top:12px;font-size:15px;line-height:25px;color:var(--muted)}

/* reviews */
.review-card{position:absolute;top:2952px;height:181px;background:#fff;border:1px solid #eef0f0;box-shadow:0 2px 8px rgba(0,0,0,.04);text-align:center;padding:24px 22px 0}
.review-card.active{border-color:#d7dadb;box-shadow:0 4px 14px rgba(0,0,0,.12)}
.review-card p{margin-top:14px;font-style:italic;font-size:11.5px;line-height:22px;color:var(--muted)}
.reviewer{position:absolute;top:3156px;display:flex;align-items:center;gap:10px}
.avatar{width:40px;height:40px;border-radius:50%;background:linear-gradient(#c9b8aa,#8e7c70)}
.reviewer b{display:block;font-weight:400;font-size:15px;color:var(--ink)}
.reviewer small{display:block;font-size:10px;color:var(--muted)}
.dot{position:absolute;top:3253px;width:8px;height:8px;border-radius:50%;background:#d9dcdd}

/* work */
.work-tile{position:absolute}
.work-label{position:absolute;bottom:26px;font-family:'Montserrat',sans-serif;font-weight:800;font-size:17px;color:#fff;letter-spacing:.5px}

/* faq */
.faq-item{position:absolute;left:249px;width:743px;border-radius:8px;background:#253238;color:#fff;font-size:14.5px;letter-spacing:.2px}
.faq-head{height:45px;display:flex;align-items:center;justify-content:space-between;padding:0 26px 0 40px}
.faq-item.open{background:var(--sage-dark)}
.faq-body{padding:4px 60px 0 46px;font-size:14.5px;line-height:25px;color:#fff}

/* footer */
.footer{left:0;top:4472px;width:1200px;height:587px;background:var(--footer)}
.footer-brand{left:143px;top:4600px;width:200px;height:180px;display:flex;flex-direction:column;align-items:center;justify-content:center;gap:16px;font-family:'Montserrat',sans-serif;font-weight:800;font-size:30px;color:#e8ecec}
.footer-brand span.mark{width:40px;height:40px;background:#e8ecec}
.footer h4{position:absolute;font-family:'Roboto',sans-serif;font-weight:700;font-size:16px;color:#fff}
.contact-line{position:absolute;left:434px;display:flex;gap:16px;color:#fff;font-size:13px;line-height:21px}
.ring{flex:none;width:32px;height:32px;border-radius:50%;border:1.5px solid #fff;display:flex;align-items:center;justify-content:center}
.social-ring{position:absolute;top:4793px;width:26px;height:26px;border-radius:50%;border:1.5px solid #fff}
.form-panel{left:754px;top:4551px;width:322px;height:331px;background:var(--footer-panel)}
.field{position:absolute;left:788px;width:266px;height:28px;border:1px solid #c7cfd2;color:#fff;font-size:12px;padding:6px 8px}
.copyright{left:0;top:4996px;width:1200px;text-align:center;color:#fff;font-size:13px}
</style>
</head>
<body>

<!-- Top bar -->
<div class="abs topbar-left">
  <span class="social-dot" style="left:143px"></span>
  <span class="social-dot" style="left:171px"></span>
  <span class="social-dot" style="left:199px"></span>
  <span class="social-dot" style="left:227px"></span>
</div>
<div class="abs topbar-right">
  <svg width="14" height="11" viewBox="0 0 14 11"><rect x="0.5" y="0.5" width="13" height="10" fill="#fff"/><path d="M0.5 0.8 7 6 13.5 0.8" stroke="#27343a" fill="none"/></svg>
  <span>hello@ktplumbing-demo.com</span><span>|</span>
  <svg width="14" height="14" viewBox="0 0 24 24"><path fill="#fff" d="M6.6 10.8a15 15 0 0 0 6.6 6.6l2.2-2.2c.3-.3.7-.4 1-.2 1.1.4 2.3.6 3.6.6.6 0 1 .4 1 1V20c0 .6-.4 1-1 1A17 17 0 0 1 3 4c0-.6.4-1 1-1h3.5c.6 0 1 .4 1 1 0 1.3.2 2.5.6 3.6.1.3 0 .7-.2 1z"/></svg>
  <span>+1 555 010 2400</span>
</div>

<!-- Navigation -->
<header class="abs nav">
  <div class="brand"><span class="brand-mark"></span>KT Plumbing</div>
  <span class="menu active" style="left:455px">HOME</span>
  <span class="menu" style="left:525px">ABOUT</span>
  <span class="menu" style="left:600px">OUR SERVICES</span>
  <span class="menu" style="left:727px">PROJECTS</span>
  <span class="menu" style="left:827px">FAQ</span>
  <div class="btn" style="left:894px;top:29px;width:159px;height:43px;font-size:13px">CONTACT US</div>
</header>

<!-- Hero -->
<div class="abs hero-photo" role="img" aria-label="Plumber in a red cap and checked shirt fixing a kitchen sink tap"></div>
<div class="abs hero-card"></div>
<div class="abs hero-title">EXPERT PLUMBING<br>SOLUTIONS</div>
<div class="abs hero-sub">Emergency repairs, commercial installations, and long-term service contracts.</div>
<div class="btn" style="left:652px;top:536px;width:216px;height:51px">REQUEST SERVICE</div>

<!-- About -->
<h2 class="abs about-title">ABOUT US</h2>
<div class="abs about-text">
  KT Plumbing Division offers clients design, fabrication, and installation for commercial and industrial plumbing systems. As part of a MEP package or stand-alone, our team self-performs process piping, domestic water, medical gas, natural gas, waste/vent, and storm drainage systems.<br>
  Nemo enim ipsam voluptatem quia voluptas sit aspernatur aut odit aut fugit, sed quia consequuntur magni dolores eos qui ratione voluptatem sequi nesque porro quisquam
</div>
<div class="abs about-photo" role="img" aria-label="Three plumbers standing in front of a white service van"></div>
<div class="btn" style="left:145px;top:1237px;width:159px;height:51px">CONTACT US</div>

<!-- Services -->
<div class="abs services-band"></div>
<h2 class="section-title" style="top:1518px">OUR SERVICES</h2>
<div class="abs services-sub">Our Expertise</div>

<div class="service-card" style="left:145px;top:1665px;height:169px">
  <svg width="52" height="52" viewBox="0 0 52 52" fill="none" stroke="#6e767a" stroke-width="1.5"><rect x="8" y="12" width="16" height="32"/><rect x="28" y="12" width="16" height="32"/><path d="M8 20h36M14 6v6M38 6v6M12 38h8M32 38h8"/></svg>
  <span>Commercial Plumbing<br>Services</span>
</div>
<div class="service-card raised" style="left:454px;top:1665px;height:169px">
  <svg width="52" height="52" viewBox="0 0 52 52" fill="none" stroke="#6e767a" stroke-width="1.5"><path d="M24 6 8 12v12c0 10 7 17 16 20 9-3 16-10 16-20V12z"/><path d="M24 16c-4 5-5 7-5 9a5 5 0 0 0 10 0c0-2-1-4-5-9z"/><circle cx="38" cy="38" r="8"/><path d="m34 38 3 3 5-6"/></svg>
  <span>Leak Detection Services</span>
</div>
<div class="service-card" style="left:762px;top:1665px;height:169px">
  <svg width="64" height="52" viewBox="0 0 64 52" fill="none" stroke="#6e767a" stroke-width="1.5"><circle cx="32" cy="16" r="10"/><path d="M32 26v8M4 34h56v8H4zM4 34v8M60 34v8M24 34v-4h16v4"/></svg>
  <span>Leak Cooling Services</span>
</div>
<div class="service-card" style="left:145px;top:1854px;height:167px">
  <svg width="52" height="52" viewBox="0 0 52 52" fill="none" stroke="#6e767a" stroke-width="1.5"><rect x="16" y="4" width="20" height="26" rx="3"/><path d="M26 10c-3 4-4 6-4 8a4 4 0 0 0 8 0c0-2-1-4-4-8zM12 36c8 4 20 4 28 0M8 42c10 5 26 5 36 0"/></svg>
  <span>Water Detection Services</span>
</div>
<div class="service-card" style="left:454px;top:1854px;height:167px">
  <svg width="64" height="56" viewBox="0 0 64 56" fill="none" stroke="#6e767a" stroke-width="1.5"><path d="M6 12h52v8H6zM22 20v12h20V20M28 32v8h8v-8"/><circle cx="32" cy="6" r="3"/><path d="M50 28c-2 3-3 4-3 6a3 3 0 0 0 6 0c0-2-1-3-3-6zM32 46c-2 3-3 4-3 6a3 3 0 0 0 6 0c0-2-1-3-3-6z"/></svg>
  <span>Leak Scaning Services</span>
</div>
<div class="service-card" style="left:762px;top:1854px;height:167px">
  <svg width="52" height="52" viewBox="0 0 52 52" fill="none" stroke="#6e767a" stroke-width="1.5"><path d="M10 44V18a8 8 0 0 1 16 0v8a6 6 0 0 0 12 0V8M4 44h12M34 8h10M16 14v30"/></svg>
  <span>Barnet Plumbing Services</span>
</div>

<!-- Why choose us -->
<h2 class="section-title" style="top:2258px">WHY CHOOSE US</h2>

<div class="why-item" style="left:142px;top:2380px">
  <svg width="52" height="52" viewBox="0 0 52 52" fill="none" stroke="#c8663f" stroke-width="1.6"><circle cx="26" cy="26" r="20"/><text x="26" y="30" text-anchor="middle" font-family="Roboto,sans-serif" font-size="11" fill="#c8663f" stroke="none">24/7</text></svg>
  <h3>24/7 Response</h3>
  <p>Nemo enim ipsam voluptatem<br>quia voluptaspernatur</p>
</div>
<div class="why-item" style="left:451px;top:2380px">
  <svg width="52" height="52" viewBox="0 0 52 52" fill="none" stroke="#c8663f" stroke-width="1.6"><rect x="12" y="6" width="14" height="10"/><path d="M16 16v30h6V16M14 24h10M14 32h10"/><circle cx="38" cy="14" r="7"/><path d="M38 10v5M38 17v1"/></svg>
  <h3>Leak Detection</h3>
  <p>Nemo enim ipsam voluptatem<br>quia voluptaspernatur</p>
</div>
<div class="why-item" style="left:759px;top:2380px">
  <svg width="52" height="52" viewBox="0 0 52 52" fill="none" stroke="#c8663f" stroke-width="1.6"><path d="M26 4 10 12v12c0 10 7 17 16 22 9-5 16-12 16-22V12z"/><path d="M18 22l8-6 8 6v12H18z"/><path d="M24 34v-6h4v6"/></svg>
  <h3>Our Premises</h3>
  <p>Nemo enim ipsam voluptatem<br>quia voluptaspernatur</p>
</div>
<div class="why-item" style="left:142px;top:2567px">
  <svg width="52" height="52" viewBox="0 0 52 52" fill="none" stroke="#c8663f" stroke-width="1.6"><circle cx="26" cy="24" r="16"/><path d="M14 40c4 4 20 4 24 0M20 24l4 4 8-8"/><path d="M6 20h4M42 20h4"/></svg>
  <h3>Our Service</h3>
  <p>Nemo enim ipsam voluptatem<br>quia voluptaspernatur</p>
</div>
<div class="why-item" style="left:451px;top:2567px">
  <svg width="52" height="52" viewBox="0 0 52 52" fill="none" stroke="#c8663f" stroke-width="1.6"><path d="M26 4 10 10v14c0 10 7 18 16 22 9-4 16-12 16-22V10z"/><path d="M18 24l6 6 11-11"/></svg>
  <h3>Our Warranties</h3>
  <p>Nemo enim ipsam voluptatem<br>quia voluptaspernatur</p>
</div>
<div class="why-item" style="left:759px;top:2567px">
  <svg width="60" height="52" viewBox="0 0 60 52" fill="none" stroke="#c8663f" stroke-width="1.6"><path d="M4 26h52v10H4zM4 26v10M56 26v10M22 26V14h16v12M26 14V8h8v6"/><circle cx="44" cy="14" r="4"/></svg>
  <h3>Lorem Isum Sod</h3>
  <p>Nemo enim ipsam voluptatem<br>quia voluptaspernatur</p>
</div>

<!-- Reviews -->
<h2 class="section-title" style="top:2850px">CUSTOMER REVIEWS</h2>

<svg width="0" height="0" style="position:absolute">
  <defs><polygon id="star" points="8,0 10.4,5.2 16,5.8 11.8,9.6 13,15.2 8,12.4 3,15.2 4.2,9.6 0,5.8 5.6,5.2" fill="#c8663f"/></defs>
</svg>

<div class="review-card" style="left:134px;width:302px">
  <svg width="96" height="16" viewBox="0 0 96 16"><use href="#star" x="0"/><use href="#star" x="20"/><use href="#star" x="40"/><use href="#star" x="60"/><use href="#star" x="80"/></svg>
  <p>Lorem ipsum dolor sit amet, consectetur adipiscing elit, sed do eiusmod tempor incididunt ut labore et dolore magna aliqu enim ad minim veniam,ullamco laboris nisi ut aliquip ex ea commodoullamco laboris nisi</p>
</div>
<div class="review-card active" style="left:450px;width:304px">
  <svg width="96" height="16" viewBox="0 0 96 16"><use href="#star" x="0"/><use href="#star" x="20"/><use href="#star" x="40"/><use href="#star" x="60"/><use href="#star" x="80"/></svg>
  <p>Lorem ipsum dolor sit amet, consectetur adipiscing elit, sed do eiusmod tempor incididunt ut labore et dolore magna aliqu enim ad minim veniam,ullamco laboris nisi ut aliquip ex ea commodoullamco laboris nisi</p>
</div>
<div class="review-card" style="left:770px;width:296px">
  <svg width="96" height="16" viewBox="0 0 96 16"><use href="#star" x="0"/><use href="#star" x="20"/><use href="#star" x="40"/><use href="#star" x="60"/><use href="#star" x="80"/></svg>
  <p>Lorem ipsum dolor sit amet, consectetur adipiscing elit, sed do eiusmod tempor incididunt ut labore et dolore magna aliqu enim ad minim veniam,ullamco laboris nisi ut aliquip ex ea commodoullamco laboris nisi</p>
</div>

<div class="reviewer" style="left:210px"><span class="avatar" role="img" aria-label="Reviewer portrait"></span><div><b>Owen Hale</b><small>orem ipsu</small></div></div>
<div class="reviewer" style="left:524px"><span class="avatar" role="img" aria-label="Reviewer portrait"></span><div><b>Nora Vance</b><small>orem ipsu</small></div></div>
<div class="reviewer" style="left:846px"><span class="avatar" role="img" aria-label="Reviewer portrait"></span><div><b>Marco Bellini</b><small>orem ipsu</small></div></div>

<span class="dot" style="left:575px;background:#a8adb0"></span>
<span class="dot" style="left:596px"></span>
<span class="dot" style="left:617px"></span>

<!-- Recent work -->
<h2 class="section-title" style="top:3358px">OUR RECENT WORK</h2>

<div class="work-tile" style="left:0;top:3470px;width:285px;height:213px;background:linear-gradient(135deg,#d7dadb,#8f989d 50%,#3b5c8a 80%,#c9a43c)" role="img" aria-label="Wrench tightening a chrome pipe fitting"></div>
<div class="work-tile" style="left:0;top:3700px;width:285px;height:210px;background:linear-gradient(180deg,#eceae6,#d9d4cc 45%,#5a6470 75%,#2f4f7a)" role="img" aria-label="Plumber working under a kitchen sink cabinet"></div>
<div class="work-tile" style="left:304px;top:3470px;width:285px;height:440px;background:linear-gradient(160deg,#2a1d17 0%,#6b4b3b 35%,#e4e7ea 55%,#8d9499 80%,#3a2a22 100%)" role="img" aria-label="Leaking white drain pipe before repair">
  <span class="work-label" style="left:45px">BEFORE</span>
</div>
<div class="work-tile" style="left:609px;top:3470px;width:285px;height:440px;background:linear-gradient(200deg,#b8bec2 0%,#6d7478 40%,#d8dcde 60%,#3a3e41 100%)" role="img" aria-label="Chrome sink trap after repair">
  <span class="work-label" style="left:52px">AFTER</span>
</div>
<div class="abs" style="left:566px;top:3657px;width:66px;height:66px;border-radius:50%;background:#fff;display:flex;align-items:center;justify-content:center">
  <svg width="30" height="16" viewBox="0 0 30 16" fill="none" stroke="#1f2326" stroke-width="2"><path d="M9 2 3 8l6 6M21 2l6 6-6 6"/></svg>
</div>
<div class="work-tile" style="left:915px;top:3470px;width:285px;height:213px;background:linear-gradient(135deg,#e6e1da,#c7bfb4 50%,#6f6a66 75%,#e9e6e1)" role="img" aria-label="Plumber kneeling beside a radiator"></div>
<div class="work-tile" style="left:915px;top:3700px;width:285px;height:210px;background:linear-gradient(135deg,#b8352c,#c9a24a 40%,#e6e6e4 65%,#9a9ea0)" role="img" aria-label="Brass manifold with red valves"></div>

<!-- FAQ -->
<h2 class="section-title" style="top:4014px">FAQ</h2>

<div class="faq-item" style="top:4101px">
  <div class="faq-head"><span>NEMO ENIM IPSAM VOLUPTR AUT ODIT AUR MAGNI DOLORES?</span>
    <svg width="16" height="10" viewBox="0 0 16 10" fill="none" stroke="#fff" stroke-width="2"><path d="m2 2 6 6 6-6"/></svg></div>
</div>
<div class="faq-item" style="top:4159px">
  <div class="faq-head"><span>NEMO ENIM IPSAM VOLUPTR AUT ODIT AUR MAGNI DOLORES?</span>
    <svg width="16" height="10" viewBox="0 0 16 10" fill="none" stroke="#fff" stroke-width="2"><path d="m2 2 6 6 6-6"/></svg></div>
</div>
<div class="faq-item open" style="top:4215px;height:166px">
  <div class="faq-head" style="height:62px"><span>NEMO ENIM IPSAM VOLUPTR AUT ODIT AUR MAGNI DOLORES?</span>
    <svg width="16" height="10" viewBox="0 0 16 10" fill="none" stroke="#fff" stroke-width="2"><path d="m2 8 6-6 6 6"/></svg></div>
  <div class="faq-body">Nemo enim ipsam voluptatem quia voluptas sit aspernatur aut odit aut fugit, sed quia consequuntur magni doloruptatem quia voluptas sit aspernatur aut odit aut fugit, sed quia consequuntur magni doloruptatem quia voluptas sit aspernatur</div>
</div>

<!-- Footer -->
<footer class="abs footer">
  <div class="abs footer-brand" style="top:128px"><span class="mark"></span>KT Plumbing</div>

  <h4 style="left:434px;top:120px">Contact Us</h4>
  <div class="contact-line" style="top:168px">
    <span class="ring"><svg width="12" height="16" viewBox="0 0 12 16"><path fill="#fff" d="M6 0a6 6 0 0 0-6 6c0 4.5 6 10 6 10s6-5.5 6-10a6 6 0 0 0-6-6zm0 8.5A2.5 2.5 0 1 1 6 3.5a2.5 2.5 0 0 1 0 5z"/></svg></span>
    <div>4820 Larkfield Road<br>Brenmoor, CA 95000<br>72 Quarry Lane<br>Halden, NV 89000</div>
  </div>
  <div class="contact-line" style="top:266px">
    <span class="ring"><svg width="14" height="14" viewBox="0 0 24 24"><path fill="#fff" d="M6.6 10.8a15 15 0 0 0 6.6 6.6l2.2-2.2c.3-.3.7-.4 1-.2 1.1.4 2.3.6 3.6.6.6 0 1 .4 1 1V20c0 .6-.4 1-1 1A17 17 0 0 1 3 4c0-.6.4-1 1-1h3.5c.6 0 1 .4 1 1 0 1.3.2 2.5.6 3.6.1.3 0 .7-.2 1z"/></svg></span>
    <div>General Inquiries: 555-014-7720<br>Service Department: 555-019-3364</div>
  </div>
  <span class="social-ring" style="left:434px;top:321px"></span>
  <span class="social-ring" style="left:469px;top:321px"></span>
  <span class="social-ring" style="left:503px;top:321px"></span>
  <span class="social-ring" style="left:537px;top:321px"></span>
  <span class="social-ring" style="left:571px;top:321px"></span>

  <div class="abs" style="left:133px;top:468px;width:934px;height:1px;background:#3f4d53"></div>
</footer>

<div class="abs form-panel"></div>
<h4 class="abs" style="left:786px;top:4590px;font-weight:700;font-size:16px;color:#fff">Get In Touch:</h4>
<div class="field" style="top:4631px">Name</div>
<div class="field" style="top:4673px">Email</div>
<div class="field" style="top:4715px;display:flex;justify-content:space-between">Service
  <svg width="10" height="8" viewBox="0 0 10 8" fill="none" stroke="#fff" stroke-width="1.5"><path d="m1 2 4 4 4-4"/></svg></div>
<div class="field" style="top:4757px;height:54px">Message</div>
<div class="btn" style="left:796px;top:4831px;width:72px;height:26px;font-size:11px">SUBMIT</div>

<div class="abs copyright">Copyrights © 2026 KT Plumbing. All Rights Reserved. &nbsp;|&nbsp; Privacy Policy &nbsp;|&nbsp; Terms of Use</div>

</body>
</html>
```